UI/ UX Design for ERP Software

We need a new UX/UI interface for a ERP software for property managers. Our CMMS / ERP solution is made based on responsive design technologies and is coded in PHP.
The overall UX to be similar to Tev Ulna - easy navigation, intuitive menus.

Industry/Entity Type

Property Management

Number of Pages Required

5+ page

Requirements
Must have
• Round dock buttons
Consistent icons across the application
Enough Spacing between buttons/icons/ menu
Consistent Font
Nice to have
• We would like the UX to allow the users to use the application without /minimum training.
Should not have
• we don't want anything that is classic with respect to UX

```html
<!DOCTYPE html>
<html lang="en">
<head>
<meta charset="utf-8">
<title>Domora — Property ERP Dashboard</title>
<link href="https://fonts.googleapis.com/css2?family=Poppins:wght@400;500;600;700;800&display=swap" rel="stylesheet">
<style>
:root{
  --sky-top:#00b8ff;
  --sky-bottom:#1b84ff;
  --brand:#1e8eff;
  --ink:#394456;
  --ink-soft:#5b6576;
  --muted:#959dab;
  --side:#536075;
  --side-line:#61708a;
  --canvas:#f4f5f8;
  --field:#eef0f4;
  --line:#e7eaef;
  --white:#ffffff;
  --up:#4fbf45;
  --down:#f03c55;
  --pink:#f25fa8;
  --orange:#ff8a3d;
  --violet:#9b5cf6;
  --mint:#3ecf8e;
  --azure:#2f9bff;
  --edit:#5bc45a;
  --cyan-cell:#bfeef3;
  --lilac-cell:#d3cbf6;
  --rose-cell:#f9cfcf;
  --avatar-dark:#46556b;
}
*{box-sizing:border-box;margin:0;padding:0}
html,body{width:1200px;height:2271px;overflow:hidden}
body{font-family:"Poppins",sans-serif;color:var(--ink)}
.board{position:relative;width:1200px;height:2271px;overflow:hidden;background:linear-gradient(180deg,var(--sky-top) 0%,#129cff 45%,var(--sky-bottom) 100%)}
.backdrop{position:absolute;inset:0}
.hero-title{position:absolute;top:40px;left:0;width:100%;text-align:center;font-size:172px;font-weight:800;line-height:1.1;color:var(--white);letter-spacing:-4px}
.section-no{position:absolute;left:231px;font-size:40px;font-weight:800;color:var(--white);line-height:1}

.screen{position:absolute;left:233px;width:734px;height:489px;border-radius:26px;background:var(--canvas);overflow:hidden;box-shadow:0 30px 50px -20px rgba(10,60,160,.45)}
.topbar{position:absolute;left:0;top:0;width:100%;height:53px;background:var(--white)}
.logo{position:absolute;left:22px;top:13px;display:flex;align-items:center;gap:6px;font-size:17px;font-weight:600;color:var(--brand)}
.logo-mark{width:16px;height:16px;border-radius:3px;background:var(--brand)}
.search{position:absolute;left:169px;top:15px;width:138px;height:23px;border-radius:12px;background:var(--field);font-size:7.5px;color:var(--muted);padding:0 12px;display:flex;align-items:center;justify-content:space-between}
.sort{position:absolute;left:317px;top:15px;width:58px;height:23px;border-radius:12px;background:var(--field);font-size:7.5px;color:var(--muted);padding:0 10px;display:flex;align-items:center;justify-content:space-between}
.tool-btn{position:absolute;top:13px;width:26px;height:26px;border-radius:8px;background:var(--field);display:flex;align-items:center;justify-content:center;color:var(--ink-soft)}
.tool-btn .dot{position:absolute;top:7px;right:8px;width:4px;height:4px;border-radius:50%;background:var(--down)}
.bar-divider{position:absolute;left:632px;top:14px;width:1px;height:24px;background:var(--line)}
.avatar{position:absolute;top:14px;width:25px;height:25px;border-radius:50%;border:2px solid var(--white)}
.avatar.a1{left:649px;background:linear-gradient(160deg,#c98b5b,#2e3a2a)}
.avatar.a2{left:667px;background:linear-gradient(160deg,#b9a3e6,#d8a07c)}
.avatar-add{position:absolute;left:686px;top:14px;width:25px;height:25px;border-radius:50%;background:var(--avatar-dark);border:2px solid var(--white);color:var(--white);font-size:14px;line-height:20px;text-align:center}
.icon{width:12px;height:12px;fill:none;stroke:currentColor;stroke-width:1.4;stroke-linecap:round;stroke-linejoin:round}

.sidebar{position:absolute;left:0;top:53px;width:153px;height:436px;background:var(--side)}
.nav{position:absolute;left:10px;top:25px;width:124px;list-style:none}
.nav li{position:relative;height:32.8px;display:flex;align-items:center;gap:8px;padding-left:10px;font-size:8px;font-weight:500;color:var(--white);white-space:nowrap}
.nav li::after{content:"";position:absolute;left:12px;right:0;bottom:0;height:1px;background:var(--side-line);opacity:.6}
.nav li.active{height:26px;margin-bottom:6.8px;border-radius:13px;background:var(--brand);font-size:9.5px;font-weight:600}
.nav li.active::after{display:none}
.nav .more{position:absolute;right:-5px;width:11px;height:11px;border-radius:50%;background:#8591a4;color:var(--white);font-size:8px;line-height:11px;text-align:center}
.side-scroll{position:absolute;left:142px;top:182px;width:2px;height:40px;border-radius:1px;background:#3f4a5c}

.page-title{position:absolute;left:174px;top:75px;font-size:17px;font-weight:700;color:var(--ink)}
.stat{position:absolute;top:108px;width:104px;height:88px;border-radius:4px;background:var(--white);overflow:hidden}
.stat .delta{position:absolute;right:10px;top:10px;font-size:6.5px;font-weight:600}
.stat .delta.up{color:var(--up)}
.stat .delta.down{color:var(--down)}
.stat .label{position:absolute;left:9px;top:23px;font-size:7.5px;color:var(--muted)}
.stat .value{position:absolute;left:9px;top:33px;font-size:9.5px;font-weight:600;color:var(--ink)}
.stat svg{position:absolute;left:0;bottom:0;width:104px;height:42px}

.panel{position:absolute;background:var(--white);border-radius:4px}
.activity{left:174px;top:210px;width:540px;height:229px}
.activity svg{position:absolute;inset:0}
.footer-note{position:absolute;left:153px;right:0;top:468px;text-align:center;font-size:8px;font-weight:500;color:var(--ink-soft)}

.crumbs{position:absolute;right:20px;top:85px;display:flex;align-items:center;gap:5px;font-size:7.5px;font-weight:600;color:var(--ink-soft)}
.info{left:174px;top:113px;width:540px;height:390px}
.info h3,.assigned h3,.cal-title{font-size:11px;font-weight:600;color:var(--ink)}
.info .h-left{position:absolute;left:21px;top:17px}
.info .h-right{position:absolute;left:341px;top:17px}
.edit-btn{position:absolute;left:151px;top:14px;width:92px;height:22px;border-radius:11px;background:var(--edit);color:var(--white);font-size:7.5px;font-weight:600;display:flex;align-items:center;justify-content:center;gap:4px}
.facts{position:absolute;left:21px;top:51px;width:282px;list-style:none}
.facts li{height:21.9px;display:flex;align-items:center;font-size:7px;padding-left:13px}
.facts li:nth-child(even){background:var(--canvas)}
.facts li::before{content:"";width:4px;height:4px;border-radius:50%;border:1.3px solid var(--brand);margin-right:7px}
.facts .k{width:106px;font-weight:600;color:var(--ink);text-transform:uppercase}
.facts .v{color:var(--ink-soft)}
.info-scroll{position:absolute;left:312px;top:200px;width:3px;height:28px;border-radius:2px;background:#d8dce3}
.photo{position:absolute;left:342px;width:176px;height:130px;border-radius:3px}
.photo.p1{top:49px;background:linear-gradient(160deg,#e9eff4 0%,#c9d6e0 55%,#7d93a8 100%)}
.photo.p2{top:186px;background:linear-gradient(200deg,#e4ebf1 0%,#d2dde6 50%,#9fb1c2 100%)}
.photo.p3{top:323px;background:linear-gradient(180deg,#d9e6ef 0%,#eef3f7 100%)}
.photo-scroll{position:absolute;left:525px;top:214px;width:3px;height:73px;border-radius:2px;background:#d8dce3}

.assigned{position:absolute;left:21px;top:86px;width:212px}
.thumbs{position:absolute;left:0;top:25px;display:flex;gap:5px}
.thumb{width:40px;text-align:center;font-size:6px;color:var(--muted)}
.thumb .shot{width:40px;height:40px;border-radius:3px;margin-bottom:3px}
.shot.t1{background:linear-gradient(160deg,#c4d4e2,#4b5a6b)}
.shot.t2{background:linear-gradient(160deg,#9fd3ff,#1c6fd1)}
.shot.t3{background:linear-gradient(160deg,#e3d7c4,#5f7fa7)}
.shot.t4{background:linear-gradient(160deg,#d5ecff,#163f8a)}
.list-title{position:absolute;left:0;font-size:6.8px;font-weight:500;color:var(--ink-soft);white-space:nowrap}
.grid-table{position:absolute;left:0;border-collapse:collapse;background:var(--white);font-size:6px;color:var(--muted);table-layout:fixed}
.grid-table th{height:21px;font-weight:400;border:1px solid var(--line)}
.grid-table td{height:17px;border:1px solid var(--line)}
.narrow{width:164px}
.wide{width:207px}

.cal-heading{position:absolute;left:243px;top:86px;font-size:11px;font-weight:600;color:var(--ink)}
.calendar{left:244px;top:111px;width:470px;height:400px}
.cal-title{position:absolute;left:17px;top:17px;font-size:11.5px}
.cal-date{position:absolute;left:296px;top:24px;font-size:6.8px;color:var(--ink-soft)}
.cal-view{position:absolute;left:338px;top:17px;width:58px;height:21px;border-radius:11px;background:var(--canvas);font-size:7px;color:var(--muted);display:flex;align-items:center;justify-content:space-between;padding:0 8px}
.cal-nav{position:absolute;top:18px;width:19px;height:19px;border-radius:50%;border:1px solid var(--line);display:flex;align-items:center;justify-content:center;color:var(--ink-soft)}
.month{position:absolute;left:0;top:50px;width:470px;display:grid;grid-template-columns:74px 67px 62px 65px 65px 63px 74px;grid-template-rows:35px repeat(6,55px)}
.month .dow{display:flex;align-items:center;justify-content:center;font-size:7.5px;font-weight:600;color:var(--ink-soft);border-top:1px solid var(--line);border-bottom:1px solid var(--line)}
.month .day{position:relative;border-right:1px solid var(--line);border-bottom:1px solid var(--line);font-size:8px;color:var(--ink-soft);text-align:right;padding:7px 7px 0 0}
.month .day:nth-child(7n){border-right:0}
.month .event{position:absolute;left:6px;right:4px;bottom:6px;text-align:left;font-size:6px;line-height:1.35;color:#3d4a5e}
.day.hatch{background:repeating-linear-gradient(135deg,#fff 0 4px,#eceef2 4px 5px)}
.day.cyan{background:var(--cyan-cell)}
.day.lilac{background:var(--lilac-cell)}
.day.rose{background:var(--rose-cell)}
</style>
</head>
<body>
<svg width="0" height="0" style="position:absolute" aria-hidden="true">
  <defs>
    <symbol id="i-gauge" viewBox="0 0 16 16"><circle cx="8" cy="8" r="6.5"/><path d="M8 8l3-3M4.5 10.5h7"/></symbol>
    <symbol id="i-users" viewBox="0 0 16 16"><circle cx="6" cy="5.5" r="2.7"/><path d="M1.5 14c0-3 2-4.5 4.5-4.5s4.5 1.5 4.5 4.5M10.5 3a2.5 2.5 0 010 5M12 9.8c1.6.5 2.5 2 2.5 4.2"/></symbol>
    <symbol id="i-home" viewBox="0 0 16 16"><path d="M2 7.5L8 2l6 5.5M3.5 6.5V14h9V6.5"/></symbol>
    <symbol id="i-house" viewBox="0 0 16 16"><path d="M2 7.5L8 2l6 5.5M3.5 6.5V14h9V6.5"/><circle cx="8" cy="9" r="1.6"/><path d="M5.5 13c.4-1.5 1.3-2.2 2.5-2.2s2.1.7 2.5 2.2"/></symbol>
    <symbol id="i-contact" viewBox="0 0 16 16"><rect x="2.5" y="1.5" width="11" height="13" rx="1.5"/><circle cx="8" cy="6.5" r="2"/><path d="M5 12c.5-1.8 1.6-2.6 3-2.6s2.5.8 3 2.6"/></symbol>
    <symbol id="i-worker" viewBox="0 0 16 16"><path d="M4.5 6a3.5 3.5 0 017 0z"/><circle cx="8" cy="8" r="2.5"/><path d="M2.5 15c0-3 2.4-4.5 5.5-4.5s5.5 1.5 5.5 4.5z"/></symbol>
    <symbol id="i-doc" viewBox="0 0 16 16"><circle cx="5" cy="8" r="3.5"/><path d="M9 3h5v10H9M10.5 6h2M10.5 8.5h2M10.5 11h2"/></symbol>
    <symbol id="i-tools" viewBox="0 0 16 16"><path d="M2 2l5 5M9 9l5 5M14 2l-4 4M6 10l-4 4M2 2h2v2M12 12l2 2"/></symbol>
    <symbol id="i-edit" viewBox="0 0 16 16"><rect x="2" y="2" width="12" height="12" rx="1.5"/><path d="M5 11l1-3 5-5 2 2-5 5z"/></symbol>
    <symbol id="i-cart" viewBox="0 0 16 16"><path d="M3 3h10l-1 6H4zM4 9l-.5 3h9"/><circle cx="5" cy="14" r=".9"/><circle cx="11" cy="14" r=".9"/><path d="M8 1v5"/></symbol>
    <symbol id="i-bell" viewBox="0 0 16 16"><path d="M4 11V7a4 4 0 018 0v4l1.5 1.5h-11zM6.5 14h3"/></symbol>
    <symbol id="i-chat" viewBox="0 0 16 16"><path d="M2 2.5h12v8.5H7l-3 2.5v-2.5H2zM5 5.5h6M5 8h4"/></symbol>
    <symbol id="i-folder" viewBox="0 0 16 16"><path d="M1.5 3.5h5l1.5 1.5h6.5v8.5h-13z"/><circle cx="9" cy="9" r="2"/><path d="M10.5 10.5l1.8 1.8"/></symbol>
    <symbol id="i-search" viewBox="0 0 16 16"><circle cx="7" cy="7" r="4.5"/><path d="M10.5 10.5l3.5 3.5"/></symbol>
    <symbol id="i-chev" viewBox="0 0 16 16"><path d="M5 6.5l3 3 3-3"/></symbol>
    <symbol id="i-left" viewBox="0 0 16 16"><path d="M13 8H3M6.5 4.5L3 8l3.5 3.5"/></symbol>
    <symbol id="i-right" viewBox="0 0 16 16"><path d="M3 8h10M9.5 4.5L13 8l-3.5 3.5"/></symbol>
    <symbol id="i-pen" viewBox="0 0 16 16"><rect x="2" y="2" width="12" height="12" rx="1.5"/><path d="M5 11l1-3 5-5 2 2-5 5z"/></symbol>
    <linearGradient id="fill-pink" x1="0" y1="0" x2="0" y2="1"><stop offset="0" stop-color="#f25fa8" stop-opacity=".35"/><stop offset="1" stop-color="#f25fa8" stop-opacity="0"/></linearGradient>
    <linearGradient id="fill-orange" x1="0" y1="0" x2="0" y2="1"><stop offset="0" stop-color="#ff8a3d" stop-opacity=".35"/><stop offset="1" stop-color="#ff8a3d" stop-opacity="0"/></linearGradient>
    <linearGradient id="fill-violet" x1="0" y1="0" x2="0" y2="1"><stop offset="0" stop-color="#9b5cf6" stop-opacity=".35"/><stop offset="1" stop-color="#9b5cf6" stop-opacity="0"/></linearGradient>
    <linearGradient id="fill-mint" x1="0" y1="0" x2="0" y2="1"><stop offset="0" stop-color="#3ecf8e" stop-opacity=".35"/><stop offset="1" stop-color="#3ecf8e" stop-opacity="0"/></linearGradient>
    <linearGradient id="fill-azure" x1="0" y1="0" x2="0" y2="1"><stop offset="0" stop-color="#2f9bff" stop-opacity=".35"/><stop offset="1" stop-color="#2f9bff" stop-opacity="0"/></linearGradient>
  </defs>
</svg>

<main class="board">
  <svg class="backdrop" width="1200" height="2271" viewBox="0 0 1200 2271" aria-hidden="true">
    <path d="M0 680 C180 520 420 470 640 470 L1200 470 L1200 2271 L0 2271Z" fill="#2aa3ff" opacity=".45"/>
    <path d="M0 1580 C120 1380 300 1250 560 1230 C800 1210 1020 1240 1200 1200 L1200 2271 L0 2271Z" fill="#6cbcff" opacity=".35"/>
    <path d="M0 1760 C200 1640 500 1600 1200 1640 L1200 2271 L0 2271Z" fill="#1a84ff" opacity=".55"/>
  </svg>

  <h1 class="hero-title">Domora</h1>

  <!-- Screen 1: dashboard -->
  <div class="section-no" style="top:330px">01</div>
  <section class="screen" style="top:391px">
    <header class="topbar">
      <div class="logo"><span class="logo-mark"></span>Domora</div>
      <div class="search">Search...<svg class="icon" style="color:#394456"><use href="#i-search"/></svg></div>
      <div class="sort">A–Z<svg class="icon" style="width:9px"><use href="#i-chev"/></svg></div>
      <div class="tool-btn" style="left:513px"><svg class="icon"><use href="#i-bell"/></svg><span class="dot"></span></div>
      <div class="tool-btn" style="left:552px"><svg class="icon"><use href="#i-chat"/></svg></div>
      <div class="tool-btn" style="left:591px"><svg class="icon"><use href="#i-folder"/></svg></div>
      <span class="bar-divider"></span>
      <span class="avatar a1" role="img" aria-label="Team member avatar"></span>
      <span class="avatar a2" role="img" aria-label="Team member avatar"></span>
      <span class="avatar-add">+</span>
    </header>
    <nav class="sidebar">
      <ul class="nav">
        <li class="active"><svg class="icon"><use href="#i-gauge"/></svg>Dashboard</li>
        <li><svg class="icon"><use href="#i-users"/></svg>Customers</li>
        <li><svg class="icon"><use href="#i-home"/></svg>Properties</li>
        <li><svg class="icon"><use href="#i-house"/></svg>Tenant</li>
        <li><svg class="icon"><use href="#i-contact"/></svg>Contact</li>
        <li><svg class="icon"><use href="#i-worker"/></svg>Contractors</li>
        <li><svg class="icon"><use href="#i-users"/></svg>Employees</li>
        <li><svg class="icon"><use href="#i-doc"/></svg>Compliance Manag...</li>
        <li><svg class="icon"><use href="#i-tools"/></svg>Prevent. Mainten...<span class="more">+</span></li>
        <li><svg class="icon"><use href="#i-edit"/></svg>Work Orders<span class="more">+</span></li>
        <li><svg class="icon"><use href="#i-cart"/></svg>Purchase Orders</li>
        <li><svg class="icon"><use href="#i-home"/></svg>Property Inspections</li>
      </ul>
      <span class="side-scroll"></span>
    </nav>

    <h2 class="page-title">Active Dashboard</h2>

    <article class="stat" style="left:174px">
      <span class="delta up">+09.84% ↗</span><span class="label">Properties</span><span class="value">3 homes</span>
      <svg viewBox="0 0 104 42"><path d="M6 40 C16 34 22 36 30 30 S42 28 50 22 S62 10 72 12 S86 24 104 18 V42 H6Z" fill="url(#fill-pink)"/><path d="M6 40 C16 34 22 36 30 30 S42 28 50 22 S62 10 72 12 S86 24 104 18" fill="none" stroke="var(--pink)" stroke-width="1.3"/></svg>
    </article>
    <article class="stat" style="left:283px">
      <span class="delta down">+09.84% ↗</span><span class="label">Tenants</span><span class="value">8 Tenants</span>
      <svg viewBox="0 0 104 42"><path d="M22 40 C30 34 34 30 40 30 S50 24 56 20 S70 10 80 12 S94 18 104 20 V42 H22Z" fill="url(#fill-orange)"/><path d="M22 40 C30 34 34 30 40 30 S50 24 56 20 S70 10 80 12 S94 18 104 20" fill="none" stroke="var(--orange)" stroke-width="1.3"/></svg>
    </article>
    <article class="stat" style="left:392px">
      <span class="delta up">+09.84% ↗</span><span class="label">Properties Area</span><span class="value">422,000.00 sq.ft</span>
      <svg viewBox="0 0 104 42"><path d="M22 40 C30 32 36 30 44 24 S56 24 62 16 S78 8 86 14 S98 22 104 18 V42 H22Z" fill="url(#fill-violet)"/><path d="M22 40 C30 32 36 30 44 24 S56 24 62 16 S78 8 86 14 S98 22 104 18" fill="none" stroke="var(--violet)" stroke-width="1.3"/></svg>
    </article>
    <article class="stat" style="left:501px">
      <span class="delta down">+09.84% ↗</span><span class="label">Rented Area</span><span class="value">233,500.00 sq.ft</span>
      <svg viewBox="0 0 104 42"><path d="M22 40 C30 32 36 34 42 26 S54 30 60 22 S72 12 80 14 S94 20 104 18 V42 H22Z" fill="url(#fill-mint)"/><path d="M22 40 C30 32 36 34 42 26 S54 30 60 22 S72 12 80 14 S94 20 104 18" fill="none" stroke="var(--mint)" stroke-width="1.3"/></svg>
    </article>
    <article class="stat" style="left:610px">
      <span class="delta up">+09.84% ↗</span><span class="label">Vacancies Area</span><span class="value">188,500.00 sq.ft</span>
      <svg viewBox="0 0 104 42"><path d="M22 40 C30 30 34 26 40 24 S52 28 58 20 S72 8 82 12 S96 14 104 10 V42 H22Z" fill="url(#fill-azure)"/><path d="M22 40 C30 30 34 26 40 24 S52 28 58 20 S72 8 82 12 S96 14 104 10" fill="none" stroke="var(--azure)" stroke-width="1.3"/></svg>
    </article>

    <section class="panel activity">
      <svg viewBox="0 0 540 229" font-family="Poppins, sans-serif">
        <g fill="none" stroke="#394456" stroke-width="1"><rect x="17" y="21" width="11" height="10" rx="1"/><path d="M17 24.5h11M20 19.5v3M25 19.5v3"/></g>
        <text x="34" y="29" font-size="7.5" fill="#394456">12-27-2021 - 01-03-2021</text>
        <g font-size="6.5" font-weight="500" fill="#5b6576" text-anchor="middle">
          <rect x="139" y="18" width="59" height="16" rx="8" fill="#eef0f4"/><text x="168.5" y="28.5">Last 7 days</text>
          <rect x="205" y="18" width="57" height="16" rx="8" fill="#eef0f4"/><text x="233.5" y="28.5">Last months</text>
          <rect x="269" y="18" width="60" height="16" rx="8" fill="#eef0f4"/><text x="299" y="28.5">Last 3 months</text>
          <rect x="336" y="18" width="55" height="16" rx="8" fill="#eef0f4"/><text x="363.5" y="28.5">Next 7 days</text>
          <rect x="398" y="18" width="60" height="16" rx="8" fill="#eef0f4"/><text x="428" y="28.5">Next months</text>
          <rect x="464" y="18" width="58" height="16" rx="8" fill="#eef0f4"/><text x="493" y="28.5">Next 3 months</text>
        </g>
        <g font-size="4.5" fill="#959dab" text-anchor="middle">
          <text x="18" y="62">10K</text><text x="18" y="83">08K</text><text x="18" y="104">06K</text><text x="18" y="126">04K</text><text x="18" y="148">02K</text><text x="18" y="170">0</text>
        </g>
        <g stroke="#eef0f4" stroke-width=".6"><path d="M30 61h490M30 82h490M30 103h490M30 125h490M30 147h490"/></g>
        <g fill="var(--brand)">
          <rect x="37" y="112" width="2.4" height="56"/><rect x="53" y="136" width="2.4" height="32"/><rect x="69" y="156" width="2.4" height="12"/><rect x="85" y="108" width="2.4" height="60"/><rect x="100" y="131" width="2.4" height="37"/><rect x="116" y="120" width="2.4" height="48"/><rect x="132" y="156" width="2.4" height="12"/><rect x="148" y="92" width="2.4" height="76"/><rect x="164" y="163" width="2.4" height="5"/><rect x="180" y="131" width="2.4" height="37"/><rect x="196" y="120" width="2.4" height="48"/><rect x="212" y="149" width="2.4" height="19"/><rect x="227" y="131" width="2.4" height="37"/><rect x="243" y="149" width="2.4" height="19"/><rect x="259" y="152" width="2.4" height="16"/><rect x="275" y="105" width="2.4" height="63"/><rect x="291" y="136" width="2.4" height="32"/><rect x="307" y="115" width="2.4" height="53"/><rect x="323" y="96" width="2.4" height="72"/><rect x="339" y="136" width="2.4" height="32"/><rect x="354" y="159" width="2.4" height="9"/><rect x="370" y="73" width="2.4" height="95"/><rect x="386" y="112" width="2.4" height="56"/><rect x="402" y="145" width="2.4" height="23"/><rect x="418" y="117" width="2.4" height="51"/><rect x="434" y="92" width="2.4" height="76"/><rect x="450" y="127" width="2.4" height="41"/><rect x="466" y="163" width="2.4" height="5"/><rect x="481" y="159" width="2.4" height="9"/><rect x="497" y="127" width="2.4" height="41"/><rect x="513" y="143" width="2.4" height="25"/>
        </g>
        <g font-size="4.5" fill="#959dab" text-anchor="middle">
          <text x="38" y="177">01</text><text x="54" y="177">02</text><text x="70" y="177">03</text><text x="86" y="177">04</text><text x="101" y="177">05</text><text x="117" y="177">06</text><text x="133" y="177">07</text><text x="149" y="177">08</text><text x="165" y="177">09</text><text x="181" y="177">10</text><text x="197" y="177">11</text><text x="213" y="177">12</text><text x="228" y="177">13</text><text x="244" y="177">14</text><text x="260" y="177">15</text><text x="276" y="177">16</text><text x="292" y="177">17</text><text x="308" y="177">18</text><text x="324" y="177">19</text><text x="340" y="177">20</text><text x="355" y="177">21</text><text x="371" y="177">22</text><text x="387" y="177">23</text><text x="403" y="177">24</text><text x="419" y="177">25</text><text x="435" y="177">26</text><text x="451" y="177">27</text><text x="467" y="177">28</text><text x="482" y="177">29</text><text x="498" y="177">30</text><text x="514" y="177">31</text>
        </g>
        <g font-size="6.3" fill="#5b6576">
          <circle cx="44" cy="194" r="2" fill="#2fb4ff"/><text x="49" y="196.5">Scheduled Maintenance</text>
          <circle cx="150" cy="194" r="2" fill="#6cc94f"/><text x="155" y="196.5">Completed Scheduled Maintenance</text>
          <circle cx="296" cy="194" r="2" fill="#ff8a3d"/><text x="301" y="196.5">Future Scheduled Maintenance</text>
          <circle cx="424" cy="194" r="2" fill="#f25f8a"/><text x="429" y="196.5">Scheduled Work Orders</text>
          <circle cx="44" cy="209" r="2" fill="#9aa2ad"/><text x="49" y="211.5">Completed Work Orders</text>
          <circle cx="150" cy="209" r="2" fill="#ffc53d"/><text x="155" y="211.5">Property Inspections In Progress</text>
          <circle cx="296" cy="209" r="2" fill="#9b5cf6"/><text x="301" y="211.5">Completed Property Inspections</text>
          <circle cx="424" cy="209" r="2" fill="#3ecfb0"/><text x="429" y="211.5">Scheduled Work Orders</text>
        </g>
      </svg>
    </section>
    <p class="footer-note">2019 copyrights © Domora</p>
  </section>

  <!-- Screen 2: property details -->
  <div class="section-no" style="top:945px">02</div>
  <section class="screen" style="top:1006px">
    <header class="topbar">
      <div class="logo"><span class="logo-mark"></span>Domora</div>
      <div class="search">Search...<svg class="icon" style="color:#394456"><use href="#i-search"/></svg></div>
      <div class="sort">A–Z<svg class="icon" style="width:9px"><use href="#i-chev"/></svg></div>
      <div class="tool-btn" style="left:513px"><svg class="icon"><use href="#i-bell"/></svg><span class="dot"></span></div>
      <div class="tool-btn" style="left:552px"><svg class="icon"><use href="#i-chat"/></svg></div>
      <div class="tool-btn" style="left:591px"><svg class="icon"><use href="#i-folder"/></svg></div>
      <span class="bar-divider"></span>
      <span class="avatar a1" role="img" aria-label="Team member avatar"></span>
      <span class="avatar a2" role="img" aria-label="Team member avatar"></span>
      <span class="avatar-add">+</span>
    </header>
    <nav class="sidebar">
      <ul class="nav">
        <li class="active"><svg class="icon"><use href="#i-gauge"/></svg>General Info</li>
        <li><svg class="icon"><use href="#i-users"/></svg>Organization Chart</li>
        <li><svg class="icon"><use href="#i-home"/></svg>Tenant List</li>
        <li><svg class="icon"><use href="#i-house"/></svg>Property Assets</li>
        <li><svg class="icon"><use href="#i-contact"/></svg>Contractors List</li>
        <li><svg class="icon"><use href="#i-worker"/></svg>Compliance Manag...</li>
        <li><svg class="icon"><use href="#i-users"/></svg>Maint. Work Orders</li>
        <li><svg class="icon"><use href="#i-doc"/></svg>Work Orders</li>
        <li><svg class="icon"><use href="#i-cart"/></svg>Purchase Orders</li>
        <li><svg class="icon"><use href="#i-edit"/></svg>Files</li>
      </ul>
    </nav>

    <h2 class="page-title">Crest Tower</h2>
    <div class="crumbs"><svg class="icon" style="width:10px;height:10px;fill:#394456;stroke:none"><use href="#i-home"/></svg>HOME<span>/</span>PROPERTIES</div>

    <section class="panel info">
      <h3 class="h-left">General Information</h3>
      <span class="edit-btn"><svg class="icon" style="width:9px;height:9px"><use href="#i-pen"/></svg>PROPERTY EDIT</span>
      <h3 class="h-right">General Information</h3>
      <ul class="facts">
        <li><span class="k">Province:</span><span class="v">British Columbia</span></li>
        <li><span class="k">City:</span><span class="v">Acton Vale</span></li>
        <li><span class="k">Address:</span><span class="v">48 Harbourline Way, Vancouver, BC</span></li>
        <li><span class="k">GPS Address:</span><span class="v">49.2801133 : -123-10455200000001</span></li>
        <li><span class="k">Postal Code:</span><span class="v">V6k 2R8</span></li>
        <li><span class="k">Date Built:</span><span class="v">07/01/1980</span></li>
        <li><span class="k">Area (sq.ft):</span><span class="v">150000.00</span></li>
        <li><span class="k">Lot Size:</span><span class="v"></span></li>
        <li><span class="k">Zoning:</span><span class="v">CDI</span></li>
        <li><span class="k">Structure Type:</span><span class="v">Seel and concreate</span></li>
        <li><span class="k">Building Height:</span><span class="v">250</span></li>
        <li><span class="k">Clear Height:</span><span class="v"></span></li>
        <li><span class="k">Floor Loading Capacity:</span><span class="v">50</span></li>
        <li><span class="k">Number of Floors:</span><span class="v">30</span></li>
        <li><span class="k">Suites:</span><span class="v">150</span></li>
      </ul>
      <span class="info-scroll"></span>
      <div class="photo p1" role="img" aria-label="Photo of the tower facade with angular glass volumes"></div>
      <div class="photo p2" role="img" aria-label="Photo of the tower's tiled corner rising into the sky"></div>
      <div class="photo p3" role="img" aria-label="Photo of a white building detail"></div>
      <span class="photo-scroll"></span>
    </section>
  </section>

  <!-- Screen 3: assignments and calendar -->
  <div class="section-no" style="top:1550px">02</div>
  <section class="screen" style="top:1611px">
    <header class="topbar">
      <div class="logo"><span class="logo-mark"></span>Domora</div>
      <div class="search">Search...<svg class="icon" style="color:#394456"><use href="#i-search"/></svg></div>
      <div class="sort">A–Z<svg class="icon" style="width:9px"><use href="#i-chev"/></svg></div>
      <div class="tool-btn" style="left:513px"><svg class="icon"><use href="#i-bell"/></svg><span class="dot"></span></div>
      <div class="tool-btn" style="left:552px"><svg class="icon"><use href="#i-chat"/></svg></div>
      <div class="tool-btn" style="left:591px"><svg class="icon"><use href="#i-folder"/></svg></div>
      <span class="bar-divider"></span>
      <span class="avatar a1" role="img" aria-label="Team member avatar"></span>
      <span class="avatar a2" role="img" aria-label="Team member avatar"></span>
      <span class="avatar-add">+</span>
    </header>

    <section class="assigned">
      <h3>Assigned properties</h3>
      <div class="thumbs">
        <div class="thumb"><div class="shot t1" role="img" aria-label="Property 1 photo"></div>Propert 1</div>
        <div class="thumb"><div class="shot t2" role="img" aria-label="Property 2 photo"></div>Propert 2</div>
        <div class="thumb"><div class="shot t3" role="img" aria-label="Property 3 photo"></div>Propert 3</div>
        <div class="thumb"><div class="shot t4" role="img" aria-label="Property 4 photo"></div>Propert 4</div>
      </div>
      <p class="list-title" style="top:94px">Open&nbsp; Tenant Requests Assigned To User 3 Requets</p>
      <table class="grid-table narrow" style="top:108px">
        <tr><th>Ticket ID</th><th>Subject</th><th>Property</th><th>Tenant</th></tr>
        <tr><td></td><td></td><td></td><td></td></tr>
        <tr><td></td><td></td><td></td><td></td></tr>
      </table>
      <p class="list-title" style="top:169px">Open Maintenance Assigned To User - 5 Tickets</p>
      <table class="grid-table wide" style="top:183px">
        <tr><th></th><th>ID</th><th>Property</th><th>Template</th><th>Date</th></tr>
        <tr><td></td><td></td><td></td><td></td><td></td></tr>
        <tr><td></td><td></td><td></td><td></td><td></td></tr>
      </table>
      <p class="list-title" style="top:245px">Open Wo Assigned To User - 3</p>
      <table class="grid-table narrow" style="top:259px">
        <tr><th>Wo Name</th><th>Property</th><th>Date</th><th>Status</th></tr>
        <tr><td></td><td></td><td></td><td></td></tr>
        <tr><td></td><td></td><td></td><td></td></tr>
      </table>
      <p class="list-title" style="top:320px">Purchase Orders Status (Last 5)</p>
      <table class="grid-table wide" style="top:333px">
        <tr><th>Po</th><th>Property</th><th>Cost</th><th>Created</th><th>Approved</th></tr>
        <tr><td></td><td></td><td></td><td></td><td></td></tr>
        <tr><td></td><td></td><td></td><td></td><td></td></tr>
      </table>
    </section>

    <h3 class="cal-heading">Maintenance and wo calendar</h3>
    <section class="panel calendar">
      <h4 class="cal-title">Calendar</h4>
      <span class="cal-date">15-01-2021</span>
      <span class="cal-view">Month<svg class="icon" style="width:9px"><use href="#i-chev"/></svg></span>
      <span class="cal-nav" style="left:417px"><svg class="icon" style="width:9px"><use href="#i-left"/></svg></span>
      <span class="cal-nav" style="left:442px"><svg class="icon" style="width:9px"><use href="#i-right"/></svg></span>
      <div class="month">
        <div class="dow">SUN</div><div class="dow">MON</div><div class="dow">TUE</div><div class="dow">WED</div><div class="dow">THU</div><div class="dow">FRI</div><div class="dow">SAT</div>
        <div class="day">1</div><div class="day hatch">2</div><div class="day">3</div><div class="day">4</div><div class="day">5</div><div class="day">6</div><div class="day">7</div>
        <div class="day">8</div><div class="day">9</div><div class="day">10</div><div class="day cyan">11<span class="event"># Ashford court Gatelink</span></div><div class="day">12</div><div class="day">13</div><div class="day">14</div>
        <div class="day">15</div><div class="day lilac">16<span class="event">#1106 cook<br>daily inspection</span></div><div class="day">17</div><div class="day">18</div><div class="day">19</div><div class="day lilac">20<span class="event">#1106 cook<br>daily inspection</span></div><div class="day">21</div>
        <div class="day">22</div><div class="day">23</div><div class="day">24</div><div class="day rose">25<span class="event">#1106 cook<br>daily inspection</span></div><div class="day">26</div><div class="day">27</div><div class="day">28</div>
        <div class="day">29</div><div class="day">30</div><div class="day">31</div><div class="day">1</div><div class="day">2</div><div class="day">3</div><div class="day">4</div>
        <div class="day">5</div><div class="day">6</div><div class="day">7</div><div class="day">8</div><div class="day">9</div><div class="day">10</div><div class="day">11</div>
      </div>
    </section>
  </section>
</main>
</body>
</html>
```